Yard sign

Looking for a yard sign. <br/>Something simple, name, number. <br/>Large text, readable from 50 feet away. <br/><br/>18 x 24 inches.

Target Market(s)

Potential homeowners thinking about going solar.

Colors

Designer to choose colors to be used in the design.

Requirements
Must have
• "WE'VE GONE SOLAR!"
Nice to have
• We are a solar company, we would like a design that compliments the homeowners decision that they went solar and encourages others to do the same.

```html
<!DOCTYPE html>
<html lang="en">
<head>
<meta charset="UTF-8">
<title>Sunvale Solar Yard Sign</title>
<link rel="stylesheet" href="https://fonts.googleapis.com/css2?family=Roboto+Condensed:wght@700&family=Roboto:wght@700&display=swap">
<style>
  :root {
    --page: #e4e4e4;
    --orange: #f7931e;
    --orange-deep: #f76722;
    --stripe: #dc4405;
    --yellow: #fec82b;
    --night: #121a2b;
    --night-soft: #1d2a44;
    --white: #ffffff;
  }
  * { margin: 0; padding: 0; box-sizing: border-box; }
  html, body {
    width: 1200px;
    height: 1200px;
    overflow: hidden;
    background: var(--page);
  }
  .yard-sign {
    position: absolute;
    left: 187px;
    top: 50px;
    width: 825px;
    height: 1100px;
    overflow: hidden;
    background: var(--orange);
  }
  .sign-backdrop {
    position: absolute;
    inset: 0;
    width: 825px;
    height: 1100px;
  }
  .brand {
    position: absolute;
    left: 0;
    top: 290px;
    width: 100%;
    display: flex;
    align-items: center;
    justify-content: center;
    gap: 24px;
  }
  .brand-dot {
    width: 90px;
    height: 90px;
    border-radius: 50%;
    background: var(--yellow);
    flex: none;
  }
  .brand-name {
    font-family: "Roboto Condensed", sans-serif;
    font-weight: 700;
    font-size: 92px;
    line-height: 1;
    color: var(--orange);
    white-space: nowrap;
  }
  .headline {
    position: absolute;
    left: 0;
    top: 455px;
    width: 100%;
    text-align: center;
    font-family: "Roboto Condensed", sans-serif;
    font-weight: 700;
    font-size: 84px;
    line-height: 1;
    color: var(--yellow);
    white-space: nowrap;
  }
  .agent-name {
    position: absolute;
    left: 0;
    top: 618px;
    width: 100%;
    text-align: center;
    font-family: "Roboto Condensed", sans-serif;
    font-weight: 700;
    font-size: 74px;
    letter-spacing: -1px;
    line-height: 1;
    color: var(--orange);
  }
  .phone-stripe {
    position: absolute;
    left: 0;
    top: 707px;
    width: 100%;
    height: 124px;
    background: var(--stripe);
  }
  .phone-icon {
    position: absolute;
    left: 50px;
    top: 726px;
    width: 86px;
    height: 86px;
  }
  .phone-number {
    position: absolute;
    left: 146px;
    top: 710px;
    width: 610px;
    text-align: center;
    font-family: "Roboto Condensed", sans-serif;
    font-weight: 700;
    font-size: 112px;
    line-height: 1.05;
    color: var(--yellow);
    white-space: nowrap;
  }
  .web-address {
    position: absolute;
    left: 0;
    top: 845px;
    width: 100%;
    text-align: center;
    font-family: "Roboto", sans-serif;
    font-weight: 700;
    font-size: 50px;
    line-height: 1.2;
    color: var(--yellow);
  }
</style>
</head>
<body>
  <main class="yard-sign">
    <svg class="sign-backdrop" viewBox="0 0 1215 1620" preserveAspectRatio="none" aria-hidden="true">
      <defs>
        <linearGradient id="night-sky" x1="0" y1="0" x2="1" y2="1">
          <stop offset="0" stop-color="#121a2b"/>
          <stop offset="0.5" stop-color="#1d2a44"/>
          <stop offset="1" stop-color="#2b2f36"/>
        </linearGradient>
      </defs>
      <rect width="1215" height="1620" fill="#f7931e"/>
      <path d="M615,0 H1215 V197 Q900,80 615,0 Z" fill="#f76722"/>
      <path d="M0,1410 Q300,1520 640,1620 H0 Z" fill="#f76722"/>
      <path d="M0,162 Q350,80 760,170 Q1000,225 1215,292 V340 H0 Z" fill="#fec82b"/>
      <path d="M0,1260 H1215 V1452 Q1050,1505 800,1487 Q400,1450 0,1352 Z" fill="#fec82b"/>
    </svg>
    <svg class="sign-backdrop" viewBox="0 0 1215 1620" preserveAspectRatio="none" role="img" aria-label="Photograph of dark rooftop solar panels at dusk">
      <path d="M0,232 Q350,140 760,205 Q1000,250 1215,320 V1382 Q1050,1460 800,1442 Q400,1410 0,1292 Z" fill="url(#night-sky)"/>
    </svg>

    <div class="brand">
      <div class="brand-dot" aria-hidden="true"></div>
      <div class="brand-name">SUNVALE SOLAR</div>
    </div>

    <div class="headline">WE'VE GONE SOLAR!</div>

    <div class="agent-name">MARCUS LANE</div>

    <div class="phone-stripe" aria-hidden="true"></div>
    <svg class="phone-icon" viewBox="0 0 86 86" aria-hidden="true">
      <circle cx="43" cy="43" r="40" fill="#f7931e" stroke="#fec82b" stroke-width="4"/>
      <path d="M25,24 q-6,4 -4,13 q5,17 22,26 q9,4 14,-2 l3,-4 q1,-3 -2,-5 l-7,-5 q-3,-2 -5,1 l-2,3 q-9,-5 -14,-14 l3,-2 q3,-2 1,-5 l-5,-7 q-2,-3 -4,1 Z" fill="#ffffff"/>
      <path d="M47,25 a14,14 0 0 1 14,14 M47,18 a21,21 0 0 1 21,21 M47,32 a7,7 0 0 1 7,7" fill="none" stroke="#ffffff" stroke-width="2.5" stroke-linecap="round"/>
    </svg>
    <div class="phone-number">555-014-2876</div>

    <div class="web-address">www.sunvalesolar.net</div>
  </main>
</body>
</html>
```